Modern Business Card

Modern professional business card with more than just logo and demographic info. Something memorable.

We are a trendy/modern chiropractic group with an emphasis on neurology, hence the minimalist-type brain logo. We want to convey that modern and technical aspect with professionalism and the elite nature of our practice environment.

```html
<!DOCTYPE html>
<html lang="en">
<head>
<meta charset="utf-8">
<title>Lumen Chiropractic – Business Card</title>
<link href="https://fonts.googleapis.com/css2?family=Cinzel:wght@400;600&family=Montserrat:wght@400&display=swap" rel="stylesheet">
<style>
  :root {
    --backdrop: #d0d1cc;
    --brand-blue: #4880c2;
    --paper: #ffffff;
    --edge-shadow: #5a5a5a;
  }
  * { margin: 0; padding: 0; box-sizing: border-box; }
  html, body { width: 1200px; height: 801px; overflow: hidden; }
  body { background: var(--backdrop); position: relative; }

  .card {
    position: absolute;
    width: 560px;
    height: 320px;
    background: var(--brand-blue);
    overflow: hidden;
    box-shadow: 0 6px 18px rgba(0,0,0,0.18);
  }

  /* Contact side */
  .card--contact { left: 50px; top: 60px; }
  .card--contact .paper-end {
    position: absolute; right: 0; top: 0;
    width: 125px; height: 100%;
    background: var(--paper);
  }
  .card--contact .emblem-shadow {
    position: absolute;
    width: 284px; height: 284px; border-radius: 50%;
    left: 284px; top: 22px;
    background: var(--edge-shadow);
  }
  .card--contact .emblem {
    position: absolute;
    width: 280px; height: 280px; border-radius: 50%;
    left: 292px; top: 16px;
    background: var(--paper);
    display: flex; align-items: center; justify-content: center;
  }
  .emblem-name {
    font-family: "Cinzel", serif;
    font-weight: 600;
    font-size: 40px;
    letter-spacing: 3px;
    color: var(--brand-blue);
  }

  .details {
    position: absolute; left: 40px; top: 120px;
    color: var(--paper);
  }
  .details__name {
    font-family: "Cinzel", serif;
    font-weight: 600;
    font-size: 19px;
    letter-spacing: 0.5px;
  }
  .details__line {
    font-family: "Montserrat", sans-serif;
    font-size: 14px;
    line-height: 21px;
    display: flex; align-items: center; gap: 8px;
  }
  .details__role { margin-bottom: 4px; }
  .details__line svg { width: 11px; height: 11px; flex: none; }
  .details__line.plain { padding-left: 0; }

  /* Brand side */
  .card--brand { left: 590px; top: 420px; }
  .brand-lockup {
    position: absolute; left: 70px; top: 110px;
    display: flex; align-items: center; gap: 18px;
    color: var(--paper);
  }
  .brand-lockup__dot {
    width: 76px; height: 76px; border-radius: 50%;
    background: var(--paper);
  }
  .brand-lockup__name {
    font-family: "Cinzel", serif;
    font-weight: 400;
    line-height: 1;
  }
  .brand-lockup__primary { display: block; font-size: 62px; letter-spacing: 3px; }
  .brand-lockup__secondary { display: block; font-size: 27px; letter-spacing: 2px; margin-top: 2px; }
</style>
</head>
<body>

<section class="card card--contact">
  <div class="paper-end"></div>
  <div class="emblem-shadow"></div>
  <div class="emblem"><span class="emblem-name">LUMEN</span></div>

  <div class="details">
    <p class="details__name">DANIEL REYES</p>
    <p class="details__line details__role">Director</p>
    <p class="details__line">118 Cedar Ridge Lane</p>
    <p class="details__line">Maple Falls, OR 97000</p>
    <p class="details__line">
      <svg viewBox="0 0 12 12" aria-hidden="true"><path d="M2.5 1 L4.5 1 L5 3.5 L3.8 4.4 Q5 7 7.6 8.2 L8.5 7 L11 7.5 L11 9.5 Q11 11 9.5 11 Q1 10 1 2.5 Q1 1 2.5 1Z" fill="#fff"/></svg>
      (555) 013-2468
    </p>
    <p class="details__line">
      <svg viewBox="0 0 12 12" aria-hidden="true"><rect x="0.8" y="2.3" width="10.4" height="7.4" fill="none" stroke="#fff" stroke-width="1.2"/><path d="M1 2.6 L6 6.6 L11 2.6" fill="none" stroke="#fff" stroke-width="1.2"/></svg>
      hello@lumenchiro.com
    </p>
    <p class="details__line">
      <svg viewBox="0 0 12 12" aria-hidden="true"><circle cx="6" cy="6" r="5.2" fill="none" stroke="#fff" stroke-width="1.1"/><ellipse cx="6" cy="6" rx="2.3" ry="5.2" fill="none" stroke="#fff" stroke-width="1"/><path d="M0.8 6 H11.2" stroke="#fff" stroke-width="1"/></svg>
      www.lumenchiro.com
    </p>
  </div>
</section>

<section class="card card--brand">
  <div class="brand-lockup">
    <span class="brand-lockup__dot"></span>
    <p class="brand-lockup__name">
      <span class="brand-lockup__primary">LUMEN</span>
      <span class="brand-lockup__secondary">CHIROPRACTIC</span>
    </p>
  </div>
</section>

</body>
</html>
```